Website and Logo Design for new niche job board.

Hello, We are an up and coming job board that is focused on LEGITIMATE companies that hire telecommuters to work from home. We are looking to build a highly interactive job board and forum/blog. The site is called TaskHarbor.com We focus on helping work at home moms, older workers and college students in work at home positions. We offer free job posting and advertising to the employer and free resume posting to the job seeker. (Free everything basically) Our revenue will be based from banner ads on the site so we will need a space on both sides of the page for those ads. 

The software we are using to build the job board part of the site can be viewed at www.plinkforge.example. It is already built! We do not need job software but a dashboard look to our main page - PLEASE pay attention to this! Do not submit a job board look as we have the job board page built!

These are the sites I like - please use these links to understand exactly the look I want

 

http://www.brightmuffins.example/

http://www.evagrant.example/

http://www.ladiesatwork.example/

https://www.findingnannies.example/index.asp?
Updates

Hi everyone- I think there might be some confusion to what we are looking for. We have the job board software through www.plinkforge.example, we are looking for the main page to be built around that. Basically we want a dashboard look with lots of little boxes to add content such as different articles,podcasts, forums,blogs,highlight different companies hiring,etc. If you can add scrolling or moving objects would be ideal. The less of a static website the better. You dont have to worry about the jobboard portion just the main page when you click on www.TaskHarbor.com, we really need it to capture peoples attention and see its a staffing firm AND a job board, forum, etc for work at home positions.  Here are some looks I am aiming for -

http://www.evagrant.example/

Please use alot of color- lime green, oranges, turquiose blue, purple, lots and lots of color please! I like more tropical colors. Thanks! I dont like red and dark colors at all. Thanks

Target Market(s)

Target customers will be both companies and individuals. The individuals will be a broad age range that are interested in working from home. The companies will be small to large corporations that have valid work from home positions.

Requirements
Must have
• I want a colorful site with moving objects and scrolling text - static sites are bland, and outdated- I am looking for a HIGHLY interactive board. Please do not just throw a template up there and expect me to like it. I am picky and want an ultra sleek design and eye catching. I can make an out of the box website myself, I have 3 other companies and did that -  PLEASE PLEASE DO NOT SHOW ME A COOKIE!
Nice to have
• Would be very nice to have the HTML sliced up for finished designs.
Should not have
• just not boring and static. Anything new and creative is where we are heading.

```html
<!DOCTYPE html>
<html lang="en">
<head>
<meta charset="utf-8">
<title>TaskHarbor — Work at Home Dashboard</title>
<link href="https://fonts.googleapis.com/css2?family=Arimo:wght@400;700&family=Open+Sans:wght@400;600&display=swap" rel="stylesheet">
<style>
:root{
  --blue:#0f9be0;
  --blue-dark:#0a79bf;
  --blue-deep:#0868a8;
  --lime:#7cc242;
  --green:#3bb54a;
  --orange:#f7a21b;
  --orange-text:#f47b20;
  --ad-grey:#857e7d;
  --page:#f1f3f4;
  --white:#ffffff;
  --nav-text:#8a8f93;
  --text-blue:#1c86c6;
}
*{box-sizing:border-box;margin:0;padding:0}
html,body{width:990px;height:1200px;overflow:hidden}
body{position:relative;background:var(--page);font-family:Arimo,Arial,sans-serif;color:var(--white)}
.abs{position:absolute}

/* header */
.header-art{left:0;top:0}
.brand{left:27px;top:43px;display:flex;align-items:center;gap:10px}
.brand-mark{width:30px;height:30px;background:var(--orange);border-radius:4px}
.brand-name{font-size:36px;font-weight:700;color:var(--white);letter-spacing:-1px}
.tagline{left:110px;top:90px;font-size:12px;font-weight:700;color:var(--white)}

.main-nav{left:25px;top:139px;list-style:none}
.main-nav li{display:flex;gap:5px;height:30px;margin-bottom:7px}
.nav-num{width:37px;background:var(--blue-dark);border-radius:3px;font-size:13px;display:flex;align-items:center;justify-content:center}
.main-nav li:first-child .nav-num{background:var(--lime)}
.nav-label{width:187px;background:linear-gradient(#fbfbfb,#e4e6e7);border:1px solid #d5d8da;border-radius:5px;color:var(--nav-text);font-size:16px;display:flex;align-items:center;padding-left:19px}

.tile{border-radius:26px;display:flex;flex-direction:column;justify-content:center;align-items:center;text-align:center;transform:rotate(-35deg);box-shadow:0 4px 10px rgba(0,0,0,.25)}
.tile-title{font-size:24px;font-weight:700;text-transform:uppercase;line-height:1}
.tile-sub{font-size:9px;font-weight:700;text-transform:uppercase;margin-top:5px;line-height:1.2}
.tile-podcasts{left:318px;top:14px;width:132px;height:124px;background:linear-gradient(135deg,#ffc033,var(--orange))}
.tile-support{left:295px;top:200px;width:126px;height:120px;background:linear-gradient(135deg,#a4d65e,var(--green))}
.tile-support .tile-title{font-size:17px;font-weight:400;transform:rotate(35deg)}
.tile-support b{font-weight:700}
.tile-cases{left:364px;top:56px;width:196px;height:190px;background:linear-gradient(135deg,#36b4ee,var(--blue-deep))}
.tile-cases .tile-title{font-size:28px;font-weight:400}
.tile-cases .tile-title b{font-weight:700}
.tile-forums{left:498px;top:160px;width:136px;height:128px;background:linear-gradient(135deg,#35d684,#12a85b)}

.login{left:802px;top:15px;width:152px}
.login-title{font-size:14px;font-weight:700;text-align:center;margin-bottom:7px}
.field{height:24px;background:var(--white);border:1px solid #9fc9e4;color:#333;font-size:12px;padding:4px 6px;margin-bottom:8px}
.field-row{display:flex;gap:6px}
.field-row .field{width:106px}
.ok-btn{width:38px;height:24px;background:linear-gradient(#f4f4f4,#cfd3d5);border:1px solid #aab;color:#555;font-size:12px;display:flex;align-items:center;justify-content:center}
.forgot{font-size:11px;color:var(--white);text-decoration:underline;margin-top:-2px;padding-left:1px}

.promo{right:36px;top:134px;text-align:right;width:360px}
.promo-title{font-size:30px;color:var(--blue-deep);letter-spacing:-.5px}
.promo-title em{font-style:normal;color:var(--orange-text)}
.promo-text{font-size:12px;font-weight:700;color:var(--blue-deep);text-transform:uppercase;line-height:1.15;margin-top:6px}
.promo-cta{font-size:24px;font-weight:700;color:var(--blue-dark);margin-top:8px}

/* content */
.card{border-radius:5px;overflow:hidden}
.feature{width:458px;height:142px;background:linear-gradient(180deg,#25b0ec,var(--blue-dark))}
.feature-img{left:17px;top:16px;width:92px;height:108px;border-radius:3px}
.feature-accent{right:0;bottom:0;width:118px;height:10px;background:var(--lime);border-top-left-radius:10px}
.feature-copy{left:140px;top:20px;width:300px}
.feature h2{font-size:25px;font-weight:700;letter-spacing:-.5px}
.feature h2 span{font-weight:400}
.feature p{font-size:11px;font-weight:700;text-transform:uppercase;line-height:1.2;margin-top:8px}
.learn{display:block;font-size:15px;font-weight:700;margin-top:6px}

.welcome{left:497px;top:392px;width:458px;height:148px;background:var(--white);border:1px solid #dcdfe1;padding:14px 24px}
.welcome h2{font-size:29px;color:var(--orange-text);font-weight:700}
.welcome p{font-size:12px;color:var(--blue);margin-top:5px;line-height:1.25}
.welcome .note{color:#666;font-size:11px;margin-top:10px;padding-left:20px;position:relative}
.welcome .note::before{content:"";position:absolute;left:0;top:1px;width:13px;height:15px;border:1px solid #999;background:#f6f3d8}
.sign{color:var(--text-blue);font-style:italic;font-size:13px;text-align:right;margin-top:2px}

.mini{width:219px;height:141px}
.mini-img{left:0;top:0;width:76px;height:141px}
.mini-copy{left:74px;top:20px;width:138px}
.mini h3{font-size:15px;font-weight:700;line-height:1.15}
.mini h3 b{font-size:20px}
.mini p{font-size:12px;line-height:1.15;margin-top:8px}
.mini-head{left:16px;top:10px;font-size:15px;font-weight:700}
.mini-icon{left:12px;top:38px;width:88px;height:92px;border-radius:4px}
.mini-text{left:110px;top:44px;width:104px;font-size:12px;line-height:1.15}

.ad{width:460px;height:94px;background:var(--ad-grey);font-family:"Open Sans",Arial,sans-serif;font-size:35px;display:flex;align-items:center;justify-content:center;letter-spacing:.5px}

.footer-nav{left:0;top:1163px;width:990px;height:37px;display:flex;justify-content:center;gap:42px;align-items:center;list-style:none}
.footer-nav li{font-size:13px;font-weight:700;display:flex;align-items:center;gap:8px}
.footer-nav li::before{content:"";width:10px;height:10px;background:#cfe9f8;border:1px solid var(--white)}
</style>
</head>
<body>

<svg class="abs header-art" width="990" height="1200" viewBox="0 0 990 1200" aria-hidden="true">
  <defs>
    <linearGradient id="headBlue" x1="0" y1="0" x2="0" y2="1">
      <stop offset="0" stop-color="#16a6e8"/><stop offset="1" stop-color="#0c86cd"/>
    </linearGradient>
    <linearGradient id="sky" x1="0" y1="0" x2="0" y2="1">
      <stop offset="0" stop-color="#4ab6ee"/><stop offset=".55" stop-color="#d9effb"/><stop offset=".75" stop-color="#ffffff"/>
    </linearGradient>
    <linearGradient id="grass" x1="0" y1="0" x2="0" y2="1">
      <stop offset="0" stop-color="#a9d64e"/><stop offset="1" stop-color="#5aa528"/>
    </linearGradient>
  </defs>
  <rect x="0" y="0" width="990" height="372" fill="url(#headBlue)"/>
  <path d="M610 0 H990 V360 H585 Q560 360 555 335 L540 230 Q600 150 610 0 Z" fill="url(#sky)"/>
  <path d="M545 300 Q750 262 990 290 V360 H585 Q560 360 552 335 Z" fill="url(#grass)"/>
  <path d="M0 118 H250 Q282 118 300 150 L410 340 Q428 372 470 372 H0 Z" fill="#ffffff"/>
  <rect x="0" y="372" width="990" height="4" fill="#e3e6e8"/>
  <path d="M0 1080 Q40 1090 60 1163 H0 Z M990 1100 Q940 1110 930 1163 H990 Z" fill="#0f9be0"/>
  <rect x="0" y="1163" width="990" height="37" fill="#0f9be0"/>
</svg>

<header>
  <div class="abs brand"><span class="brand-mark"></span><span class="brand-name">TaskHarbor</span></div>
  <div class="abs tagline">WE DEVELOP THE FUTURE</div>

  <ul class="abs main-nav">
    <li><span class="nav-num">.01</span><span class="nav-label">HOME</span></li>
    <li><span class="nav-num">.02</span><span class="nav-label">SERVICES</span></li>
    <li><span class="nav-num">.03</span><span class="nav-label">PRODUCTS</span></li>
    <li><span class="nav-num">.04</span><span class="nav-label">SUPPORT</span></li>
    <li><span class="nav-num">.05</span><span class="nav-label">CLIENTS</span></li>
    <li><span class="nav-num">.06</span><span class="nav-label">CONTACTS</span></li>
  </ul>

  <div class="abs tile tile-support"><div class="tile-title">ONLINE<br><b>SUPPORT</b></div></div>
  <div class="abs tile tile-cases"><div class="tile-title">CASE<b>STUDIES</b></div><div class="tile-sub">Lorem ipsum dolor sit amet,<br>consectetur adipisicing elit,<br>sed do eiusmod incididunt<br>ut magna aliqua. Read now</div></div>
  <div class="abs tile tile-podcasts"><div class="tile-title">Podcasts</div><div class="tile-sub">Labore et dolore<br>magna aliqua.</div></div>
  <div class="abs tile tile-forums"><div class="tile-title">Forums</div><div class="tile-sub">Labore et dolore<br>magna aliqua.</div></div>

  <form class="abs login">
    <div class="login-title">Security Entrance</div>
    <div class="field">enter your ID</div>
    <div class="field-row"><div class="field">password</div><div class="ok-btn">Ok</div></div>
    <div class="forgot">forgot password or ID?</div>
  </form>

  <div class="abs promo">
    <div class="promo-title">Make <em>ideal</em> decisions</div>
    <div class="promo-text">Lorem ipsum dolor sit amet,<br>consectetur adipisicing elit, sed do eiusmod<br>tempor incididunt ut labore et<br>dolore magna aliqua.</div>
    <div class="promo-cta">JOIN NOW!</div>
  </div>
</header>

<main>
  <article class="abs card feature" style="left:27px;top:392px">
    <div class="abs feature-img" role="img" aria-label="Illustration of a notebook and pen" style="background:linear-gradient(135deg,#6fbf3f,#2e6fb5)"></div>
    <div class="abs feature-copy"><h2>Headline <span>one</span></h2><p>Do eiusmod tempor incididunt ut labore et dolore magna aliqua. Ut enim ad minim quis nostrud exercitation laboris.</p><span class="learn">▸ LEARN MORE</span></div>
    <div class="abs feature-accent"></div>
  </article>

  <section class="abs card welcome">
    <h2>WELCOME!</h2>
    <p>Ut enim ad minim veniam, quis nostrud exercitation ullamco laboris nisi ut aliquip ex ea commodo consequat.</p>
    <p class="note">Ut enim ad minim veniam, quis nostrud exercitation ullamco laboris nisi ut aliquip ex ea commodo consequat. Duis aute irure</p>
    <div class="sign">Company Team</div>
  </section>

  <article class="abs card feature" style="left:27px;top:549px">
    <div class="abs feature-img" role="img" aria-label="Photo of a mother and children at home" style="background:linear-gradient(135deg,#f3d9b8,#c9a88a)"></div>
    <div class="abs feature-copy"><h2>Headline <span>two</span></h2><p>Excepteur sint occaecat cupidatat non proident, sunt in culpa qui officia deserunt mollit anim id est laborum.</p><span class="learn">▸ LEARN MORE</span></div>
    <div class="abs feature-accent" style="background:var(--orange)"></div>
  </article>

  <article class="abs card mini" style="left:497px;top:549px;background:linear-gradient(135deg,#9ab83d,#6f8f26)">
    <div class="abs mini-img" role="img" aria-label="Photo of a young man" style="background:linear-gradient(180deg,#d8c6b5,#8c7c6e)"></div>
    <div class="abs mini-copy"><h3>Headline<br>Here<br><b>NOW ››</b></h3><p>Ut enim ad minim veniam, quis nostrud exercitation ullamco</p></div>
  </article>

  <article class="abs card mini" style="left:736px;top:549px;background:linear-gradient(135deg,#3fb0bd,#1f8593)">
    <div class="abs mini-img" role="img" aria-label="Photo of an older woman" style="background:linear-gradient(180deg,#e8dcd2,#d45a4a)"></div>
    <div class="abs mini-copy" style="left:100px;width:112px"><h3>Headline<br>Here<br><b>NOW ››</b></h3><p>Ut enim ad minim veniam, quis exercitation</p></div>
  </article>

  <article class="abs card feature" style="left:27px;top:703px">
    <div class="abs feature-img" role="img" aria-label="Illustration of a globe with a cursor" style="background:radial-gradient(circle,#5cc6f5,#0a5aa8)"></div>
    <div class="abs feature-copy"><h2>Headline <span>three</span></h2><p>Excepteur sint occaecat cupidatat non proident, sunt in culpa qui officia deserunt mollit anim id est laborum.</p><span class="learn">▸ LEARN MORE</span></div>
    <div class="abs feature-accent"></div>
  </article>

  <article class="abs card mini" style="left:497px;top:703px;background:linear-gradient(135deg,#a98436,#7a5a22)">
    <div class="abs mini-head">HeadlineHere ››</div>
    <div class="abs mini-icon" role="img" aria-label="Illustration of a rising bar chart" style="background:linear-gradient(180deg,#e9e2cf,#c7b27a)"></div>
    <div class="abs mini-text">Ut enim ad minim veniam, quis nostrud exercitation ullamco</div>
  </article>

  <article class="abs card mini" style="left:736px;top:703px;background:linear-gradient(135deg,#a23c78,#6e2150)">
    <div class="abs mini-head">HeadlineHere ››</div>
    <div class="abs mini-icon" role="img" aria-label="Illustration of a newspaper and microphone" style="background:linear-gradient(180deg,#e4ecef,#9fb2bb)"></div>
    <div class="abs mini-text" style="top:38px">Ut enim ad minim veniam, quis nostrud exercitation ullamco</div>
  </article>

  <div class="abs ad" style="left:27px;top:860px">ADVERTISEMENTS</div>
  <div class="abs ad" style="left:495px;top:860px">ADVERTISEMENTS</div>
  <div class="abs ad" style="left:27px;top:965px">ADVERTISEMENTS</div>
  <div class="abs ad" style="left:495px;top:965px">ADVERTISEMENTS</div>
  <div class="abs ad" style="left:27px;top:1064px">ADVERTISEMENTS</div>
  <div class="abs ad" style="left:495px;top:1064px">ADVERTISEMENTS</div>
</main>

<footer>
  <ul class="abs footer-nav">
    <li>HOME</li><li>SERVICES</li><li>PRODUCTS</li><li>SUPPORT</li><li>CLIENTS</li><li>CONTACTS</li>
  </ul>
</footer>

</body>
</html>
```